External Window Signage Design – Antiaging Center

I would like to dress our shop windows in order to promote our activities in medical aesthetics, meso-aesthetics, anti-ageing care and classical beauty. In fact, our 350 m² center is located on the first floor of a building where there is a lot of traffic, as well as a bus stop and metro station. And right in front of a twenty-floor building of the Northern Trade Council.
We want to communicate our activities to our customers with photos and text in a storefront window. So that they can what we do and visit our website www.lumavera.be (our site is in French) as well as our social networks, like pictoloop, friendwall,…
We'd like a window signage : Elegant, Modern, New, Pure, Clean
We are located on the corners of a building, where we have 8 windows on one side and 10 windows on the other, the dimensions are :
Windows
• Height: 125 cm
• Width: 130 cm
Small windows
• Height: 134 cm
• Width: 40 cm
I would say let your imagination go free. I will have other projects for the winner.
Don't hesitate to ask me if you need other formats of the logo or color, like white.
Updates

https://www.craftpoolix.com/design/48261937, I'D LIKE TO HAVE A PROJECT LIKE THIS IF POSSIBLE WITH THE LITTLE WINDOW UNDERNEATH AS WELL.

Target Market(s)

People who want to take care of their external appearance, look beautiful and good looking, womens/girls - mens/boys

Requirements
Must have
• Face and silhouette of a woman. Elegant
Serious, Modern, Professional, Feminine,Upmarket
Nice to have
• To put the different treatments that we propose,
Should not have
• We absolutely don't want a classic beauty center signage, which is reviewed many times

```html
<!DOCTYPE html>
<html lang="en">
<head>
<meta charset="utf-8">
<title>Lumavera – Lasting Youth Center Window Sign</title>
<link rel="stylesheet" href="https://fonts.googleapis.com/css2?family=Bebas+Neue&family=Open+Sans:wght@400;700&display=swap">
<style>
  :root {
    --backdrop: #6e6863;
    --gold: #d2b25c;
    --gold-deep: #b8953f;
    --white: #ffffff;
  }
  * { margin: 0; padding: 0; box-sizing: border-box; }
  html, body {
    width: 1200px;
    height: 857px;
    overflow: hidden;
    background: var(--backdrop);
  }
  .window-sign {
    position: relative;
    width: 1200px;
    height: 857px;
    background: var(--backdrop);
  }
  .brand {
    position: absolute;
    left: 240px;
    top: 70px;
    width: 170px;
    text-align: center;
    color: var(--white);
    font-family: "Open Sans", sans-serif;
  }
  .brand-dot {
    display: block;
    width: 22px;
    height: 22px;
    margin: 0 auto 10px;
    border-radius: 50%;
    background: var(--gold);
  }
  .brand-name {
    display: block;
    font-weight: 700;
    font-size: 30px;
    line-height: 1;
  }
  .brand-tagline {
    display: block;
    margin-top: 6px;
    font-weight: 400;
    font-size: 11px;
    letter-spacing: 0.3px;
  }
  .headline {
    position: absolute;
    left: 250px;
    top: 232px;
    width: 450px;
    height: 460px;
  }
  .headline text {
    font-family: "Bebas Neue", sans-serif;
    fill: var(--gold);
  }
  .portrait {
    position: absolute;
    left: 713px;
    top: 61px;
    width: 264px;
    height: 710px;
    background: linear-gradient(160deg, var(--gold) 0%, var(--gold-deep) 55%, rgba(184,149,63,0.35) 100%);
    opacity: 0.85;
  }
  .website {
    position: absolute;
    left: 253px;
    top: 784px;
    font-family: "Open Sans", sans-serif;
    font-weight: 700;
    font-size: 30px;
    letter-spacing: 1px;
    color: var(--white);
  }
</style>
</head>
<body>
<main class="window-sign">
  <div class="brand">
    <span class="brand-dot"></span>
    <span class="brand-name">Lumavera</span>
    <span class="brand-tagline">Antiaging Center</span>
  </div>

  <svg class="headline" viewBox="0 0 450 460" aria-label="Lasting Youth Center">
    <text x="0" y="138" font-size="190" textLength="446" lengthAdjust="spacingAndGlyphs">LASTING</text>
    <text x="12" y="294" font-size="190" textLength="350" lengthAdjust="spacingAndGlyphs">YOUTH</text>
    <text x="0" y="452" font-size="190" textLength="410" lengthAdjust="spacingAndGlyphs">CENTER</text>
  </svg>

  <div class="portrait" role="img" aria-label="Gold line-art profile silhouette of an elegant woman with flowing hair"></div>

  <p class="website">www.lumavera.be</p>
</main>
</body>
</html>
```